Consulting business card

*1) An Overview:* The business is simply a financial transaction wherein I
offer to provide advice to financial holders of commercial real estate
mortgages (which are sub-performing or non-performing), and said holders
are desirous of selling said mortgages which I will offer advice to said
holders in the purchase of said mortgages. Please note the attached copy
of a proposed line-by-line business card which starts with the 1st line
"RKW Advisory, LLC" with the 2nd line "Purchase of Commercial Mortgage
Loan" and the 3rd line "Sub-performing and Non-performing" is my desired
copy subject to any suggested changes. Please ignore the the copy below
the aforementioned proposed card/copy as it will be activated at a later
date.and advise
*2) The Target Market:* I contact and advise senior officers in banks,
insurance companies, and financial institutions such as CEOs, CFOs, COOs,
and Loan Mitigation Officers: the senior officers are tasked with the
removal of sub-performing and non-performing commercial real estate loans
from their real estate portfolios. The desired market is targeted at $1-10
million USD and located in the US.
*3) Design Specifics: *STYLE should be conservative and be representative
of the financial market contacts; COLOR might show a rich forest green
element, a gold foil accent, and subtle black printing, however,
alternatively, silver foil accent(s) with strong black print would seem in
harmony with the services offered, however, I would appreciate any artful
suggestions; IMAGERY should be subtle (no logo can be strong enough to make
an immediate impact): the quality should make the recipient feel he/she has
just met an experienced and competent financial adviser (I have over 55
years of successful financial and business experience).
720.217.6154davidfredrickjones@gmail.com

```html
<!DOCTYPE html>
<html lang="en">
<head>
<meta charset="utf-8">
<title>RKW Advisory, LLC — Business Card</title>
<link href="https://fonts.googleapis.com/css2?family=Cutive+Mono&family=Tinos&family=Open+Sans:wght@400&display=swap" rel="stylesheet">
<style>
  :root {
    --backdrop: #e9e7e3;
    --card: #ffffff;
    --ink: #1c1c1c;
    --forest: #228b22;
    --forest-edge: #1fa81f;
    --rule: #8a8a8a;
  }
  * { margin: 0; padding: 0; box-sizing: border-box; }
  html, body {
    width: 1200px; height: 894px; overflow: hidden;
    background: var(--backdrop);
  }
  .canvas {
    position: relative; width: 1200px; height: 894px;
    display: flex; align-items: center; justify-content: center;
  }
  .card {
    position: relative; width: 900px; height: 514px;
    background: var(--card);
    box-shadow: 0 10px 30px rgba(0,0,0,0.12);
    overflow: hidden;
  }
  .card__header {
    position: absolute; top: 56px; left: 0; right: 0;
    text-align: center; color: var(--ink);
  }
  .company-name {
    font-family: "Cutive Mono", "Courier New", monospace;
    font-weight: 400;
    font-size: 56px; letter-spacing: 1px; line-height: 1;
  }
  .tagline {
    margin-top: 12px;
    font-family: "Tinos", "Times New Roman", serif;
    font-size: 27px; line-height: 1.18;
  }
  .person-name {
    position: absolute; right: 500px; top: 330px;
    font-family: "Tinos", "Times New Roman", serif;
    font-size: 56px; color: var(--forest); line-height: 1;
    white-space: nowrap;
  }
  .divider {
    position: absolute; left: 420px; top: 262px;
    width: 2px; height: 118px; background: var(--rule);
  }
  .contact {
    position: absolute; left: 452px; top: 272px;
    list-style: none;
    font-family: "Open Sans", Arial, sans-serif;
    font-size: 20px; color: var(--ink);
  }
  .contact__item {
    display: flex; align-items: center; gap: 12px;
    height: 32px; margin-bottom: 20px;
    white-space: nowrap;
  }
  .contact__icon { width: 20px; height: 20px; flex: none; }
  .card__band {
    position: absolute; left: 0; right: 0; bottom: 0; height: 82px;
    background: var(--forest);
    border-top: 3px solid var(--forest-edge);
  }
</style>
</head>
<body>
<main class="canvas">
  <article class="card">
    <header class="card__header">
      <h1 class="company-name">RKW Advisory LLC</h1>
      <p class="tagline">Purchase of Commercial Mortgage Loan<br>Sub-performing and Non-performing</p>
    </header>

    <p class="person-name">Martin Hale</p>
    <div class="divider"></div>

    <ul class="contact">
      <li class="contact__item">
        <svg class="contact__icon" viewBox="0 0 22 22" aria-hidden="true">
          <rect width="22" height="22" fill="#228b22"/>
          <path d="M7 5.5c.6-.4 1.3-.3 1.6.3l1 2c.2.5.1 1-.3 1.3l-.8.6c.6 1.3 1.6 2.3 2.9 2.9l.6-.8c.3-.4.8-.5 1.3-.3l2 1c.6.3.7 1 .3 1.6l-.8 1c-.6.7-1.6.9-2.5.5C9.4 14.4 7.6 12.6 6.4 9.8c-.4-.9-.2-1.9.5-2.5z" fill="#fff"/>
        </svg>
        <span>555.304.8827</span>
      </li>
      <li class="contact__item">
        <svg class="contact__icon" viewBox="0 0 22 22" aria-hidden="true">
          <rect width="22" height="22" fill="#228b22"/>
          <rect x="5" y="7" width="12" height="8.5" fill="none" stroke="#fff" stroke-width="1.5"/>
          <path d="M5 7l6 5 6-5" fill="none" stroke="#fff" stroke-width="1.5"/>
        </svg>
        <span>tomasheraldwick@mailbox.example</span>
      </li>
    </ul>

    <div class="card__band"></div>
  </article>
</main>
</body>
</html>
```